Business card for Crestline Bathrooms

Please design a business card for our bathroom renovation business. You can use my existing logo, but if you have an idea to modernize it, I would like to see it. Please see attached files first. I would like to use the blue and the orange theme. I like the concept of using the shower head in the logo. Please find following a design (or two) that I have been trying to create with my limited resources. That design was for a sign, but I was going to adopt it and use it as a business card as well. I like the concept of the water splash but I don’t think it “flows” nicely together with the logo. Another thought is that maybe creating the logo out of water splash could work and have a dramatic effect (like the water text and the butterfly picture attached with similar background instead of white). If the above doesn’t work I would like to see a modern simplified design. One of the attached files named as the unwanted business card has all the details that I want included in the business card. Please note that it is two sided.
Updates

I am very thankful for the designs that I have received, but they are very similar and only a couple of attempts to do something with the water splash as per my original brief. Modernizing the logo and having it made out of out of water splash with the orange as color accent could work and have a dramatic effect (like the water text and the butterfly picture attached with similar background instead of white). Please do not use the butterfly itself! This is just an example that images can be created out of water splash.

Contact Information for Business Card

all the details are on the unwonted business card file included

Colors
3176b5

Requirements
Nice to have
• Copied from the brief:
• ... maybe creating the logo out of water splash could work and have a dramatic effect (like the water text and the butterfly picture attached with similar background instead of white). Please do not use the butterfly itself!
Should not have
• I am getting designs with a butterfly. The butterfly picture was an example of creating something from a water splash. The butterfly itself has no association with anything other than the concept of creating a logo out of water splash. Sorry, I thought I was clear in the brief.

```html
<!DOCTYPE html>
<html lang="en">
<head>
<meta charset="utf-8">
<title>Crestline Bathrooms – Business Card</title>
<link href="https://fonts.googleapis.com/css2?family=Roboto:wght@400;500&family=Roboto+Condensed:wght@700&display=swap" rel="stylesheet">
<style>
  :root {
    --backdrop: #2a2a2b;
    --paper: #f2f2f2;
    --navy: #0b436f;
    --coral: #e9786b;
    --white: #ffffff;
  }
  * { margin: 0; padding: 0; box-sizing: border-box; }
  html, body { width: 1200px; height: 960px; overflow: hidden; }
  body {
    background: var(--backdrop);
    font-family: "Roboto", Arial, sans-serif;
    position: relative;
  }
  .card {
    position: absolute;
    width: 600px;
    height: 342px;
    border-radius: 16px;
    overflow: hidden;
  }
  .card--front { left: 322px; top: 108px; background: var(--paper); }
  .card--back  { left: 320px; top: 493px; background: var(--coral); color: var(--white); }

  .card__wave { position: absolute; inset: 0; }

  .brand {
    position: absolute;
    color: var(--navy);
    font-weight: 500;
    line-height: 1;
  }
  .brand__name { display: block; font-size: 46px; letter-spacing: -0.5px; }
  .brand__sub  { display: block; font-size: 22px; letter-spacing: 4px; margin-top: 6px; }
  .brand__dot {
    position: absolute;
    width: 18px; height: 18px;
    border-radius: 50%;
    background: var(--coral);
  }
  .card--front .brand { left: 40px; top: 78px; }
  .card--front .brand__dot { left: 214px; top: -6px; }

  .contact {
    position: absolute;
    right: 28px;
    top: 172px;
    text-align: right;
    color: var(--white);
  }
  .contact__name {
    font-family: "Roboto Condensed", "Arial Narrow", sans-serif;
    font-weight: 700;
    font-size: 20px;
    letter-spacing: 0.3px;
    margin-bottom: 8px;
  }
  .contact__address { font-size: 14px; line-height: 19px; margin-bottom: 9px; }
  .contact__list { list-style: none; font-size: 14px; line-height: 19px; }
  .contact__list li { display: flex; justify-content: flex-end; align-items: center; gap: 5px; }
  .contact__icon { width: 12px; height: 12px; fill: var(--white); flex: none; }

  .card--back .brand {
    left: 0; right: 0; top: 50px;
    text-align: center;
    color: var(--white);
  }
  .card--back .brand__dot { left: 386px; top: -8px; background: var(--white); }
  .services {
    position: absolute;
    left: 0; right: 0; top: 188px;
    list-style: none;
    text-align: center;
    font-size: 14px;
    line-height: 18px;
  }
  .memberships {
    position: absolute;
    left: 0; right: 0; top: 274px;
    display: flex;
    justify-content: center;
    align-items: center;
    gap: 14px;
  }
  .memberships__badge { background: var(--white); height: 30px; }
  .memberships__badge--round { width: 30px; border-radius: 8px; }
  .memberships__badge--wide { width: 110px; height: 22px; border-radius: 3px; }
  .memberships__divider { width: 1px; height: 34px; background: var(--white); }
</style>
</head>
<body>

<section class="card card--front" aria-label="Business card front">
  <svg class="card__wave" viewBox="0 0 600 342" aria-hidden="true">
    <path d="M428 0 C470 60 450 140 360 200 C285 252 240 300 238 342 L600 342 L600 0 Z" fill="var(--coral)"/>
    <path d="M452 0 C492 60 472 142 384 204 C310 256 252 300 248 342 L600 342 L600 0 Z" fill="var(--white)"/>
    <path d="M456 0 C496 60 476 142 388 204 C314 256 256 300 252 342 L600 342 L600 0 Z" fill="var(--navy)"/>
  </svg>

  <div class="brand">
    <span class="brand__dot"></span>
    <span class="brand__name">Crestline</span>
    <span class="brand__sub">Bathrooms</span>
  </div>

  <div class="contact">
    <p class="contact__name">DANIEL MERROW</p>
    <p class="contact__address">PO Box 41<br>Carrowvale 2704</p>
    <ul class="contact__list">
      <li>0400 555 182
        <svg class="contact__icon" viewBox="0 0 24 24"><path d="M6.6 10.8a15 15 0 0 0 6.6 6.6l2.2-2.2a1 1 0 0 1 1-.25 11.4 11.4 0 0 0 3.6.57 1 1 0 0 1 1 1V20a1 1 0 0 1-1 1A17 17 0 0 1 3 4a1 1 0 0 1 1-1h3.5a1 1 0 0 1 1 1c0 1.25.2 2.45.57 3.57a1 1 0 0 1-.25 1z"/></svg>
      </li>
      <li>6255 0147
        <svg class="contact__icon" viewBox="0 0 24 24"><path d="M7 1h10a2 2 0 0 1 2 2v18a2 2 0 0 1-2 2H7a2 2 0 0 1-2-2V3a2 2 0 0 1 2-2zm0 3v14h10V4z"/></svg>
      </li>
      <li>daniel@crestlinebathrooms.com.au
        <svg class="contact__icon" viewBox="0 0 24 24"><path d="M2 5h20v14H2zm2 2v.5l8 5 8-5V7z"/></svg>
      </li>
      <li>crestlinebathrooms.com.au
        <svg class="contact__icon" viewBox="0 0 24 24"><path d="M12 2a10 10 0 1 0 0 20 10 10 0 0 0 0-20zm-1 17.9A8 8 0 0 1 4.1 10L9 15v1a2 2 0 0 0 2 2zm6.9-2.5A2 2 0 0 0 16 16h-1v-3a1 1 0 0 0-1-1H8v-2h2a1 1 0 0 0 1-1V7h2a2 2 0 0 0 2-2v-.4a8 8 0 0 1 2.9 12.8z"/></svg>
      </li>
    </ul>
  </div>
</section>

<section class="card card--back" aria-label="Business card back">
  <div class="brand">
    <span class="brand__dot"></span>
    <span class="brand__name">Crestline</span>
    <span class="brand__sub">Bathrooms</span>
  </div>

  <ul class="services">
    <li>Complete Bathroom Renovations &amp; Remodelling</li>
    <li>Highly Skilled &amp; Qualified Tradespeople</li>
    <li>Professional Service From Concept To Completion</li>
    <li>All Work Guaranteed</li>
  </ul>

  <div class="memberships" aria-label="Industry memberships">
    <span class="memberships__badge memberships__badge--round"></span>
    <span class="memberships__divider"></span>
    <span class="memberships__badge memberships__badge--wide"></span>
  </div>
</section>

</body>
</html>
```